Label design - Superfood blend

We are a family owned nutrition company with big ambitions. Our goal is to develop a range of 100% natural supplements for women, inspired by nature & modern technology that helps them meet their nutritional needs while nourishing them from within. All our products are junk free because we believe that that’s how nature intended it. We also produce products through a sustainable process and only use biodegradable packaging for our products (See link - https://www.loamwrap.org.uk/biodegradable-stand-pouch-250g-kraft)

Our brand style is modern and minimalist. This same style will be reflected in our social media, website and we want it to be represented through the label designs for our product packaging.

We want some creative designers to design a label that is true to our style (See attached packaging brief with designs we like) and displays our values of Premium, High Quality, Organic Real Food supplements focused on women. I have provided examples in the attached brief, but please only use as inspiration, I dont want any of them to be copied (sorry have had my fingers burnt already !)
Updates

Hello all, Please note this design is for a LABEL and not the whole package. We will have a 500gm biodegradable brown package, and we will have a label (which is what this project is about) that will be stuck on the front. The size of the label will be a rectangle (unless you come up with a new shape) in the size 20cm * 15cm. Please do not submit designs for the WHOLE from of the package, as we dont intend to have printed packages. Regards

Hello all, I have added a new logo version to the attachments, could you please also try that version. Could you also please look at the new sliders. We are only looking for a minimlaist theme. If you dont know what that means, please do feel free to ask, I would be happy to supply examples. Minimalist designs, means clean, modern, upmarket, elegant designs. It does not use too many colors and mostly sticks to a combination of black and white with colors used sparingly. See some below for your reference anyway. https://www.pitchloft.co.uk/design/13359317 https://www.pitchloft.co.uk/design/17270649 https://www.pitchloft.co.uk/design/12584145 https://www.pitchloft.co.uk/design/12367479 https://www.snapquilt.com/search/pins/?q=minimalist%20label%20design&rs=rs&eq=&etslf=2809&term_meta[]=minimalist%7Crecentsearch%7Cundefined&term_meta[]=label%7Crecentsearch%7Cundefined&term_meta[]=design%7Crecentsearch%7Cundefined Regards

Target Market(s)

The target market is women between the age 25 to 45, based in UK (mostly based in larger cities in UK). They are typically middle class or higher and would be in demanding jobs and social lives, that requires for them to meet their nutrition needs in convenient, easy to take forms. The women would also be socially conscious and sensitive to issues like women's rights, environmental issues, healthy food, organic food and sustainability etc. I have a much more detailed customer avatar if required

Font styles to use
Serif
Sans Serif
Decorative
Script

Colors
e8e8e8
474747
1b1b1b
add136

Requirements
Must have
• The label, should look minimalist and modern, throw in some out of the box creativity and we have a winner. Creativity will definitely be of importance. Our packaging is a biodegradable brown paper stand up pouch (Example link in product description). So to make it standout from other colorful packaging - being creative would definitely help.
• Please use the color schemes provided in the brief (See attachments). But if you want to experiment I would be open to it, as long as they are still minimalist and does not stray very far from the color given in the brief :)

```html
<!DOCTYPE html>
<html lang="en">
<head>
<meta charset="utf-8">
<title>Verdanola – Rooted Glow label range</title>
<link href="https://fonts.googleapis.com/css2?family=Oswald:wght@300;400&family=Raleway:wght@400;500&display=swap" rel="stylesheet">
<style>
  :root {
    --paper: #ffffff;
    --backdrop: #f3f3f1;
    --mist: #e8e8e8;
    --graphite: #474747;
    --ink: #1b1b1b;
    --leaf: #add136;
    --leaf-soft: #cde57f;
    --leaf-haze: #eef5dc;
    --rule: #9a9a9a;
  }
  * { box-sizing: border-box; margin: 0; padding: 0; }
  html, body { width: 1200px; height: 857px; overflow: hidden; }
  body {
    background: var(--backdrop);
    font-family: "Raleway", sans-serif;
    color: var(--graphite);
  }
  .range {
    position: absolute;
    left: 55px;
    top: 253px;
    display: flex;
    gap: 30px;
  }
  .label {
    position: relative;
    width: 250px;
    height: 350px;
    background: var(--paper);
    border-radius: 6px;
    overflow: hidden;
    box-shadow: 0 2px 10px rgba(0,0,0,0.08);
  }
  .label__band {
    position: absolute;
    left: 0; top: 0;
    width: 100%;
    height: 56px;
  }
  .label__band--ink { background: linear-gradient(180deg, var(--graphite), #8c8c8c); }
  .label__band--leaf { background: linear-gradient(180deg, var(--leaf), var(--leaf-soft)); }
  .label__band--wash { background: linear-gradient(180deg, var(--leaf) 0%, #c6e07a 60%, var(--paper) 100%); }

  .label__tab {
    position: absolute;
    left: 31px; top: 32px;
    width: 188px; height: 26px;
    display: flex; align-items: center; justify-content: center;
    font-size: 9px; font-weight: 500; letter-spacing: 0.6px;
    text-transform: uppercase;
    color: var(--paper);
    z-index: 2;
  }
  .label__tab--leaf { background: var(--leaf); }
  .label__tab--ink { background: var(--ink); }
  .label__tab--outline { background: var(--leaf); outline: 1px solid rgba(255,255,255,0.8); outline-offset: -3px; }

  .brand {
    position: absolute;
    left: 31px; top: 58px;
    width: 188px; height: 42px;
    border: 1.5px solid var(--ink);
    border-top: none;
    display: flex; align-items: center; justify-content: center;
    font-size: 17px; font-weight: 400;
    letter-spacing: 5px;
    color: var(--ink);
    background: var(--paper);
  }
  .product-name {
    position: absolute;
    left: 0; top: 152px; width: 100%;
    text-align: center;
    font-family: "Oswald", sans-serif;
    font-weight: 400;
    font-size: 34px;
    letter-spacing: 1px;
    line-height: 1;
    white-space: nowrap;
  }
  .product-name--leaf { color: var(--leaf); }
  .product-name--ink { color: var(--ink); }

  .descriptor {
    position: absolute;
    left: 0; top: 206px; width: 100%;
    text-align: center;
    font-size: 10px;
    line-height: 1.35;
    color: var(--graphite);
  }
  .haze {
    position: absolute;
    left: 0; top: 196px;
    width: 100%; height: 44px;
    background: linear-gradient(180deg, rgba(255,255,255,0) 0%, var(--leaf-haze) 50%, rgba(255,255,255,0) 100%);
  }
  .certs {
    position: absolute;
    left: 0; top: 262px; width: 100%;
    display: flex; justify-content: center; gap: 26px;
  }
  .cert {
    width: 42px; height: 42px;
    border-radius: 50%;
  }
  .cert--organic { border: 2px solid var(--graphite); }
  .cert--vegan { border: 2px solid var(--leaf); }

  .net-weight {
    position: absolute;
    left: 14px; right: 14px; top: 318px;
    border-top: 1px solid var(--rule);
    padding-top: 3px;
    text-align: center;
    font-size: 7px;
    line-height: 1.3;
    color: var(--graphite);
  }
</style>
</head>
<body>
<main class="range">

  <article class="label">
    <div class="label__band label__band--ink" role="img" aria-label="Black and grey zigzag pattern band"></div>
    <div class="label__tab label__tab--leaf">Food Supplement</div>
    <div class="brand">VERDANOLA</div>
    <h1 class="product-name product-name--leaf">ROOTED GLOW</h1>
    <p class="descriptor">Organic, Plant-Based Prebiotics<br>and Superfood Blend</p>
    <div class="certs">
      <span class="cert cert--organic" role="img" aria-label="Organic certification badge"></span>
      <span class="cert cert--vegan" role="img" aria-label="Vegan certification badge"></span>
    </div>
    <p class="net-weight">Net Weight<br>500 g</p>
  </article>

  <article class="label">
    <div class="label__band label__band--leaf" role="img" aria-label="Green and white zigzag pattern band"></div>
    <div class="label__tab label__tab--ink">Food Supplement</div>
    <div class="brand">VERDANOLA</div>
    <h1 class="product-name product-name--ink">ROOTED GLOW</h1>
    <p class="descriptor">Organic, Plant-Based Prebiotics<br>and Superfood Blend</p>
    <div class="certs">
      <span class="cert cert--organic" role="img" aria-label="Organic certification badge"></span>
      <span class="cert cert--vegan" role="img" aria-label="Vegan certification badge"></span>
    </div>
    <p class="net-weight">Net Weight<br>500 g</p>
  </article>

  <article class="label">
    <div class="label__band label__band--ink" role="img" aria-label="Black and grey zigzag pattern band"></div>
    <div class="label__tab label__tab--ink">Food Supplement</div>
    <div class="brand">VERDANOLA</div>
    <h1 class="product-name product-name--leaf">ROOTED GLOW</h1>
    <p class="descriptor">Organic, Plant-Based Prebiotics<br>and Superfood Blend</p>
    <div class="certs">
      <span class="cert cert--organic" role="img" aria-label="Organic certification badge"></span>
      <span class="cert cert--vegan" role="img" aria-label="Vegan certification badge"></span>
    </div>
    <p class="net-weight">Net Weight<br>500 g</p>
  </article>

  <article class="label">
    <div class="label__band label__band--wash"></div>
    <div class="label__tab label__tab--outline">Food Supplement</div>
    <div class="brand">VERDANOLA</div>
    <h1 class="product-name product-name--ink">ROOTED GLOW</h1>
    <div class="haze" role="img" aria-label="Faint green decorative flourish behind the descriptor"></div>
    <p class="descriptor">Organic, Plant-Based Prebiotics<br>and Superfood Blend</p>
    <div class="certs">
      <span class="cert cert--organic" role="img" aria-label="Organic certification badge"></span>
      <span class="cert cert--vegan" role="img" aria-label="Vegan certification badge"></span>
    </div>
    <p class="net-weight">Net Weight<br>500 g</p>
  </article>

</main>
</body>
</html>
```